Business Card Design

Looking for business card designs for a new business. there will be two cards of the same design (both lots of information below in contact info). We would like the logo diagonally across the card with the information split above and below the logo similar to sketch. happy to look at similar alternatives
Please use same colours as in logo design

Industry/Entity Type

Business

Contact Information for Business Card

Dwight Halloran
mob - 0491 738 204
ph - 02 6148 3920
fax - 02 6148 3975
email - dwight@kestrelbeams.com.au
14 Larkmoor Road, Taminda NSW 2340

Colin Marchetti
mob - 0438 912 557
ph - 02 6148 3920
fax - 02 6148 3975
email - colin@kestrelbeams.com.au

```html
<!DOCTYPE html>
<html lang="en">
<head>
<meta charset="utf-8">
<title>Kestrel Beams – Business Cards</title>
<link rel="stylesheet" href="https://fonts.googleapis.com/css2?family=Source+Sans+3:wght@400;600;700&display=swap">
<style>
  :root {
    --teal: #008075;
    --white: #ffffff;
    --ink: #111111;
    --text-dark: #2a2a2a;
    --backdrop: #ecebe8;
    --border: #333333;
  }
  * { box-sizing: border-box; margin: 0; padding: 0; }
  html, body {
    width: 1145px; height: 1200px; overflow: hidden;
    background: var(--backdrop);
    font-family: "Source Sans 3", "Myriad Pro", Arial, sans-serif;
  }
  .canvas { position: relative; width: 1145px; height: 1200px; }

  /* Front card */
  .card-front {
    position: absolute; left: 188px; top: 21px;
    width: 945px; height: 540px;
    background: var(--teal); overflow: hidden;
  }
  .brand-pill {
    position: absolute; left: 333px; top: 27px;
    width: 612px; height: 214px;
    background: var(--white);
    border-radius: 107px 0 0 107px;
    display: flex; align-items: center; justify-content: center;
  }
  .person-pill {
    position: absolute; left: 0; top: 292px;
    width: 610px; height: 216px;
    background: var(--white);
    border-radius: 0 108px 108px 0;
  }
  .brand { display: flex; align-items: center; gap: 14px; }
  .brand-mark { width: 30px; height: 30px; background: var(--teal); }
  .brand-name {
    font-weight: 700; color: var(--ink);
    font-size: 70px; line-height: 1; letter-spacing: -0.5px;
  }
  .person-name {
    position: absolute; right: 42px; top: 56px;
    font-weight: 700; font-size: 36px; color: var(--teal);
  }
  .person-email {
    position: absolute; right: 42px; top: 135px;
    font-size: 22px; color: var(--text-dark);
    display: flex; align-items: center; gap: 8px;
  }
  .person-email svg { width: 18px; height: 16px; }
  .contact-list {
    position: absolute; left: 651px; top: 306px;
    list-style: none; color: var(--white); font-size: 22px;
  }
  .contact-list li {
    display: flex; align-items: center; gap: 6px;
    height: 36.5px;
  }
  .contact-list svg { width: 18px; height: 18px; fill: var(--white); }
  .address {
    position: absolute; left: 651px; top: 432px;
    color: var(--white); font-size: 22px; line-height: 32px;
    font-style: normal;
  }

  /* Back card */
  .card-back {
    position: absolute; left: 32px; top: 610px;
    width: 944px; height: 538px;
    background: var(--white);
    border: 1.5px solid var(--border);
  }
  .card-back .brand {
    position: absolute; left: 0; right: 0; top: 212px;
    justify-content: center;
  }
  .card-back .brand-name { font-size: 84px; }
  .card-back .brand-mark { width: 36px; height: 36px; }
  .website {
    position: absolute; left: 0; right: 0; top: 426px;
    text-align: center; font-size: 28px; letter-spacing: 3px;
    color: var(--text-dark);
  }
  .website strong { font-weight: 700; }
</style>
</head>
<body>
<div class="canvas">

  <section class="card-front">
    <div class="brand-pill">
      <div class="brand">
        <span class="brand-mark"></span>
        <span class="brand-name">Kestrel Beams</span>
      </div>
    </div>

    <div class="person-pill">
      <h1 class="person-name">Colin Marchetti</h1>
      <p class="person-email">
        <svg viewBox="0 0 18 16" aria-hidden="true"><path d="M1 6 L9 1 L17 6 V15 H1 Z" fill="var(--teal)"/><path d="M1 6 L9 11 L17 6" stroke="#fff" stroke-width="1.5" fill="none"/></svg>
        colin@kestrelbeams.com.au
      </p>
    </div>

    <ul class="contact-list">
      <li>
        <svg viewBox="0 0 18 18" aria-hidden="true"><circle cx="9" cy="9" r="8" fill="none" stroke="#fff" stroke-width="1.4"/><path d="M6 4.5 L8 7 L7 8.3 C7.6 9.7 8.4 10.5 9.7 11 L11 10 L13.5 12 L12 13.8 C8 13.5 4.5 10 4.2 6 Z"/></svg>
        02 6148 3920
      </li>
      <li>
        <svg viewBox="0 0 18 18" aria-hidden="true"><rect x="4.5" y="1" width="9" height="16" rx="1.5"/><rect x="6" y="3" width="6" height="5" fill="var(--teal)"/><rect x="6" y="10" width="6" height="5" fill="var(--teal)" opacity=".5"/></svg>
        0438 912 557
      </li>
      <li>
        <svg viewBox="0 0 18 18" aria-hidden="true"><rect x="5" y="2" width="8" height="5"/><rect x="1" y="7" width="16" height="7" rx="1.5"/><rect x="4" y="14" width="3" height="2"/><rect x="11" y="14" width="3" height="2"/></svg>
        02 6148 3975
      </li>
    </ul>

    <address class="address">
      14 Larkmoor Road<br>
      Ardlow NSW 2395
    </address>
  </section>

  <section class="card-back">
    <div class="brand">
      <span class="brand-mark"></span>
      <span class="brand-name">Kestrel Beams</span>
    </div>
    <p class="website">www.<strong>kestrelbeams</strong>.com.au</p>
  </section>

</div>
</body>
</html>
```